UL Aesthetic improvement on full website

brightneighbourhq.com
We need someone to improve the current website brightneighbourhq.com
Some designed to fail to follow isntruction and deliver. please find attached summary latest design requirement, please follow and read each of the requirements carefully and submit max two versions only. The winner would have to deliver within 5 days

Sample reference : velmorq.com/html/brightneighbour/#
(previous winner cant deliver)
*All of our wording and graphic content are updated, designer wouldn't involve in recreating any content.
Designer may use template or own material. delivery in html and implement on our WordPress server

please submit about us the project submission.
upon the winning, you have to maintain sub content / pages and submit the full site with your improved version of full websites including inner pages

Low design quality

Target Market(s)

general audience

Industry/Entity Type

social service

Number of Pages Required

5+ page

Requirements
Must have
• feeling and look similar to pobrix dot com
Nice to have
• extend the same style to other pages

```html
<!DOCTYPE html>
<html lang="en">
<head>
<meta charset="utf-8">
<title>Bright Neighbour – Social Inclusion</title>
<link href="https://fonts.googleapis.com/css2?family=Josefin+Sans:wght@600;700&family=Open+Sans:wght@400;600;700&display=swap" rel="stylesheet">
<style>
:root{
  --pink:#f2606b;
  --pink-soft:#f6e5e3;
  --ink:#1c1c1c;
  --text:#555;
  --muted:#888;
  --line:#e3e3e3;
  --white:#fff;
  --illus-a:#e9e4f3;
  --illus-b:#f7d6d9;
}
*{box-sizing:border-box;margin:0;padding:0}
html,body{width:1200px;height:4196px;overflow:hidden}
body{position:relative;background:var(--white);font-family:"Open Sans",Arial,sans-serif;color:var(--text)}
.abs{position:absolute}
.bands{position:absolute;left:0;top:0}
.heading{font-family:"Josefin Sans",Arial,sans-serif;font-weight:700;color:var(--ink);text-transform:uppercase;letter-spacing:1px}
.btn{position:absolute;background:var(--pink);color:var(--white);font-size:11px;font-weight:700;text-transform:uppercase;border-radius:20px;text-align:center;line-height:30px;height:30px;letter-spacing:.5px;white-space:nowrap}
.brand{display:flex;align-items:center;gap:8px;font-family:"Josefin Sans",Arial,sans-serif;font-weight:700;color:var(--pink);font-size:18px;white-space:nowrap}
.brand-dot{width:22px;height:22px;border-radius:50%;background:var(--pink);flex:none}
.brand.small{font-size:14px;gap:6px}
.brand.small .brand-dot{width:18px;height:18px}
/* nav */
.nav{left:452px;top:38px;display:flex;gap:22px;font-size:11px;font-weight:700;color:var(--ink);text-transform:uppercase;white-space:nowrap;z-index:2}
.nav .active{color:var(--ink);border-bottom:2px solid var(--pink);padding-bottom:3px}
/* hero */
.kicker{left:140px;top:92px;font-family:"Josefin Sans",Arial,sans-serif;font-weight:700;color:var(--pink);font-size:26px;text-transform:uppercase}
.hero-title{left:140px;top:126px;font-size:78px;line-height:84px}
.store{width:134px;height:44px;background:#111;border-radius:8px;top:290px}
.illus{background:linear-gradient(135deg,var(--illus-a),var(--illus-b));border-radius:12px}
.dots{left:142px;top:598px;display:flex;gap:8px}
.dots span{width:7px;height:7px;border-radius:50%;background:#d6c8c8}
.dots span.on{background:var(--pink)}
/* about */
.frame{left:140px;top:980px;width:470px;height:280px;background:var(--white);border-radius:10px;box-shadow:0 6px 20px rgba(0,0,0,.08);padding:12px}
.frame .illus{width:100%;height:100%;border-radius:6px}
.body-copy{font-size:13px;line-height:22px;color:var(--text)}
/* cards */
.card{background:var(--white);box-shadow:0 6px 22px rgba(0,0,0,.1);text-align:center;padding:36px 26px 0}
.card-icon{width:56px;height:56px;border-radius:50%;background:var(--pink);margin:0 auto 22px;display:flex;align-items:center;justify-content:center}
.card h3{font-family:"Josefin Sans",Arial,sans-serif;font-size:15px;color:var(--ink);margin-bottom:12px;text-transform:uppercase}
.card p{font-size:12px;line-height:19px}
/* news */
.news{width:264px;height:170px;background:var(--white);box-shadow:0 4px 16px rgba(0,0,0,.1);padding:14px}
.news-date{position:absolute;left:14px;top:14px;width:44px;height:44px;background:#6c6c6c;color:var(--white);text-align:center;font-size:15px;font-weight:700;line-height:18px;padding-top:5px}
.news-date small{display:block;font-size:8px;border-top:1px solid rgba(255,255,255,.5);line-height:14px}
.news-date.hot{background:var(--pink)}
.news h4{margin-left:56px;font-size:14px;line-height:17px;color:var(--ink);font-weight:600}
.news p{font-size:10px;line-height:15px;margin-top:16px;color:var(--muted)}
.news .more{font-size:10px;font-weight:700;color:var(--pink);margin-top:10px;text-transform:uppercase}
.partner{top:2950px;width:80px;height:32px;background:#ececf2;border-radius:4px}
.arrow{top:2954px;font-size:24px;color:#888;line-height:24px}
/* form */
.field{background:var(--white);height:34px;border:1px solid var(--line);font-size:11px;color:var(--muted);padding:10px 12px}
/* footer */
.foot-links{font-size:12px;line-height:22px;color:var(--ink)}
.social{width:16px;height:16px;border-radius:50%;background:var(--ink);top:4138px}
</style>
</head>
<body>

<svg class="bands" width="1200" height="4196" viewBox="0 0 1200 4196" aria-hidden="true">
  <path fill="#f6e5e3" d="M0 780 C180 650 360 700 520 690 C720 675 820 720 1000 690 C1100 672 1160 630 1200 600 L1200 1360 C1020 1430 760 1470 480 1410 C280 1370 120 1380 0 1450 Z"/>
  <path fill="#f6e5e3" d="M0 3120 C140 3030 260 3080 420 3070 C600 3060 720 3110 900 3080 C1040 3055 1130 3020 1200 2990 L1200 3620 C1120 3700 1000 3740 860 3730 L0 3730 Z"/>
</svg>

<!-- header -->
<div class="abs brand" style="left:40px;top:26px"><span class="brand-dot"></span>Bright Neighbour</div>
<nav class="abs nav">
  <span class="active">Home</span><span>About Us</span><span>Our Story</span><span>Social Impact</span><span>Join Us</span>
</nav>
<div class="btn" style="left:962px;top:30px;width:76px">Login</div>

<!-- hero -->
<div class="abs kicker">New way of giving</div>
<h1 class="abs heading hero-title">Social<br>Inclusion</h1>
<div class="abs store" style="left:140px" role="img" aria-label="App store download button"></div>
<div class="abs store" style="left:290px" role="img" aria-label="Play store download button"></div>
<div class="abs illus" style="left:680px;top:90px;width:430px;height:460px;border-radius:50%" role="img" aria-label="Illustration of the mobile app shown on three phones in front of a ferris wheel"></div>
<div class="abs dots"><span></span><span></span><span class="on"></span><span></span><span></span></div>

<!-- about -->
<div class="abs frame"><div class="illus" role="img" aria-label="Video still titled Mission: Create a digital cycle of kindness, showing a group of volunteers"></div></div>
<h2 class="abs heading" style="left:660px;top:1000px;font-size:46px">About Us</h2>
<p class="abs body-copy" style="left:660px;top:1072px;width:400px">Just like you, we resonate with a variety of social causes. At the core of everything, we believe that every societal challenge could be minimised linearly by being more kind to one another and showing more trust in each other, especially during these difficult times. Therefore, we digitalised the traditional concept of “Paying it Forward” to cultivate the new normal with kindness.</p>
<div class="btn" style="left:660px;top:1276px;width:86px">Read More</div>

<!-- pillars -->
<div class="abs card" style="left:144px;top:1575px;width:290px;height:228px">
  <div class="card-icon"><svg width="24" height="24" viewBox="0 0 24 24"><g fill="#fff"><rect x="2" y="2" width="5" height="5"/><rect x="9.5" y="2" width="5" height="5"/><rect x="17" y="2" width="5" height="5"/><rect x="2" y="9.5" width="5" height="5"/><rect x="9.5" y="9.5" width="5" height="5"/><rect x="17" y="9.5" width="5" height="5"/><rect x="2" y="17" width="5" height="5"/><rect x="9.5" y="17" width="5" height="5"/><rect x="17" y="17" width="5" height="5"/></g></svg></div>
  <h3>Our Philosophy</h3>
  <p>We believe in authentic social responsibility to drive kinder individuals and businesses.</p>
</div>
<div class="abs card" style="left:455px;top:1622px;width:290px;height:228px">
  <div class="card-icon"><svg width="26" height="26" viewBox="0 0 26 26"><circle cx="13" cy="13" r="11" fill="none" stroke="#fff" stroke-width="2"/><circle cx="13" cy="13" r="6" fill="none" stroke="#fff" stroke-width="2"/><circle cx="13" cy="13" r="2" fill="#fff"/></svg></div>
  <h3>Our Mission</h3>
  <p>We connect individuals and businesses to support others in need in an easy, transparent and holistic way.</p>
</div>
<div class="abs card" style="left:766px;top:1575px;width:290px;height:228px">
  <div class="card-icon"><svg width="24" height="24" viewBox="0 0 24 24"><circle cx="12" cy="12" r="10" fill="none" stroke="#fff" stroke-width="2"/><path d="M6 8 C9 9 9 13 12 13 C14 13 14 17 12 21 M15 4 C14 7 17 9 20 9" fill="none" stroke="#fff" stroke-width="2"/></svg></div>
  <h3>Our Future</h3>
  <p>Together, social impact as part of life at the heart of every consumption and business.</p>
</div>

<!-- story -->
<div class="abs illus" style="left:180px;top:1930px;width:360px;height:310px" role="img" aria-label="Illustration of people sharing gifts and hearts around a box"></div>
<h2 class="abs heading" style="left:630px;top:1990px;font-size:46px">Our Story</h2>
<p class="abs body-copy" style="left:630px;top:2062px;width:400px">Built in the 1960s, my family received generous donations and small handwritten notes containing good wishes through a newspaper fund raising for my mom’s medical expenses. I vividly remember some old yet tattered notes from strangers. We ended up with double the amount that was needed, and my parents used the remaining sum to support other patients.</p>
<div class="btn" style="left:630px;top:2276px;width:86px">Read More</div>

<!-- news -->
<h2 class="abs heading" style="left:0;top:2468px;width:1200px;text-align:center;font-size:46px">Most Popular News</h2>
<div class="abs news" style="left:148px;top:2596px">
  <div class="news-date">02<small>JAN</small></div>
  <h4>Pellentesque faucibus Ut accumsan ultric</h4>
  <p>Duis quam diam egestas a aliquet nisl volutpat feugiat dignissim congue tincid lacus vitae felis vestibulum.</p>
  <div class="more">Read More</div>
</div>
<div class="abs news" style="left:468px;top:2596px">
  <div class="news-date hot">02<small>JAN</small></div>
  <h4>Pellentesque faucibus Ut accumsan ultric</h4>
  <p>Duis quam diam egestas a aliquet nisl volutpat feugiat dignissim congue tincid lacus vitae felis vestibulum.</p>
  <div class="more">Read More</div>
</div>
<div class="abs news" style="left:788px;top:2596px">
  <div class="news-date">02<small>JAN</small></div>
  <h4>Pellentesque faucibus Ut accumsan ultric</h4>
  <p>Duis quam diam egestas a aliquet nisl volutpat feugiat dignissim congue tincid lacus vitae felis vestibulum.</p>
  <div class="more">Read More</div>
</div>
<div class="btn" style="left:556px;top:2840px;width:88px">View More</div>

<!-- partners -->
<div class="abs arrow" style="left:80px">&#8249;</div>
<div class="abs partner" style="left:140px"></div>
<div class="abs partner" style="left:250px"></div>
<div class="abs partner" style="left:370px"></div>
<div class="abs partner" style="left:490px"></div>
<div class="abs partner" style="left:600px"></div>
<div class="abs partner" style="left:710px"></div>
<div class="abs partner" style="left:820px"></div>
<div class="abs partner" style="left:940px"></div>
<div class="abs arrow" style="left:1104px">&#8250;</div>

<!-- contact -->
<h2 class="abs heading" style="left:0;top:3398px;width:1200px;text-align:center;font-size:46px">Contact Form</h2>
<div class="abs field" style="left:172px;top:3496px;width:276px">Enter Name</div>
<div class="abs field" style="left:464px;top:3496px;width:276px">Enter Email</div>
<div class="abs field" style="left:756px;top:3496px;width:272px">Enter Phone</div>
<div class="abs field" style="left:172px;top:3548px;width:856px;height:92px">Message</div>
<div class="btn" style="left:530px;top:3690px;width:140px">Submit</div>

<!-- footer -->
<div class="abs brand small" style="left:170px;top:3912px"><span class="brand-dot"></span>Bright Neighbour</div>
<div class="abs foot-links" style="left:350px;top:3900px">Home<br>About Us<br>Our Story<br>Social Impact<br>Join Us</div>
<div class="abs foot-links" style="left:530px;top:3900px">Terms and Use<br>Privacy Policy<br>Sitemap<br>Information<br>News</div>
<div class="abs heading" style="left:750px;top:3912px;font-size:15px">Sign Up Newsletter</div>
<div class="abs field" style="left:750px;top:3986px;width:180px;height:34px;border-radius:17px">Enter Email</div>
<div class="btn" style="left:924px;top:3988px;width:100px">Sign Up</div>
<div class="abs" style="left:170px;top:4112px;width:860px;height:1px;background:var(--line)"></div>
<div class="abs" style="left:170px;top:4136px;font-size:11px;color:var(--ink)">© 2022 BrightNeighbour. All rights reserved. | Privacy Policy | Terms</div>
<div class="abs social" style="left:960px"></div>
<div class="abs social" style="left:986px"></div>
<div class="abs social" style="left:1012px"></div>

</body>
</html>
```